Business Cards Design for the electrical wholesaler: clean bold dynamic :)

We need a business card design that would follow our latest brand guidelines. As an electrical wholesaler we want to bring a fresh look and feel into the industry. The design should be clean bold and dynamic. It should come alive with the renewed energy of our green colour. Our grey colour should keep things balanced and complement the notion of maturity and responsibility. We employ Lato as a corporate font however are not bound by this font and we’re open to interpretation here.

Target Market(s)

Electrical contractors

Industry/Entity Type

Business

Contact Information for Business Card

Logo
Name & Surname: Halyna Dorosh
Job Title: Director of Marketing
Email: halya.dorosh@quillmail.example
Cell phone: XXX.XXX.XXXX
Address: 20517 - 87 Ave. Edmonton, AB, Canada. T6K 4N8
Business Phone: 780.555.0184
Website: www.brovix.example

Font styles to use
Other font styles liked:
• Lato

Requirements
Must have
• Logo & website
Nice to have
• Brand elements - some of them you may find in the attached Brand Guidelines (e.g. three lines on the background signifying "W")

```html
<!DOCTYPE html>
<html lang="en">
<head>
<meta charset="utf-8">
<title>brovix business card</title>
<link href="https://fonts.googleapis.com/css2?family=Lato:wght@400;700&family=Roboto:wght@400;500&display=swap" rel="stylesheet">
<style>
  :root {
    --backdrop: #3b3b3d;
    --card: #262628;
    --green: #8fd42a;
    --grey: #c9c9c9;
    --white: #f2f2f2;
    --decor: #3a3a3c;
  }
  * { box-sizing: border-box; margin: 0; padding: 0; }
  html, body { width: 799px; height: 1200px; overflow: hidden; }
  body {
    background: var(--backdrop);
    font-family: "Roboto", Arial, sans-serif;
    position: relative;
  }
  .card {
    position: absolute;
    left: 80px;
    width: 640px;
    height: 366px;
    background: var(--card);
    border-radius: 26px;
    overflow: hidden;
  }
  .card-front { top: 110px; }
  .card-back { top: 720px; }

  .brand {
    position: absolute;
    display: flex;
    align-items: center;
    font-family: "Lato", Arial, sans-serif;
    font-weight: 700;
    color: var(--grey);
    letter-spacing: -1px;
  }
  .brand-dot {
    border-radius: 50%;
    background: var(--green);
    flex: none;
  }
  .card-front .brand {
    left: 0; right: 0; top: 0; bottom: 0;
    justify-content: center;
    font-size: 104px;
    gap: 22px;
  }
  .card-front .brand-dot { width: 70px; height: 70px; }

  .tab {
    position: absolute;
    left: -22px; top: 34px;
    width: 44px; height: 58px;
    border-radius: 50%;
    background: var(--green);
  }
  .holder { position: absolute; left: 42px; top: 38px; }
  .holder-name {
    font-family: "Lato", Arial, sans-serif;
    font-weight: 700;
    font-size: 30px;
    color: var(--green);
  }
  .holder-title { font-size: 16px; color: var(--white); margin-top: 2px; }

  .card-back .brand {
    right: 44px; top: 110px;
    font-size: 58px;
    gap: 12px;
  }
  .card-back .brand-dot { width: 38px; height: 38px; }

  .decor {
    position: absolute;
    right: -80px; bottom: -150px;
    width: 380px; height: 300px;
  }

  .contact {
    position: absolute;
    left: 40px; bottom: 34px;
    font-size: 15px;
    line-height: 1.45;
    color: var(--white);
    list-style: none;
  }
  .contact li { display: flex; align-items: center; gap: 8px; }
  .contact .address { display: block; margin-bottom: 4px; }
  .icon { width: 14px; height: 14px; flex: none; }
</style>
</head>
<body>

<section class="card card-front">
  <div class="brand"><span class="brand-dot"></span>brovix</div>
</section>

<section class="card card-back">
  <span class="tab"></span>
  <div class="holder">
    <p class="holder-name">Halyna Dorosh</p>
    <p class="holder-title">Founder &amp; CEO</p>
  </div>

  <div class="brand"><span class="brand-dot"></span>brovix</div>

  <svg class="decor" viewBox="0 0 380 300" aria-hidden="true">
    <defs>
      <linearGradient id="decorFade" x1="0" y1="0" x2="1" y2="1">
        <stop offset="0" stop-color="#333335"/>
        <stop offset="1" stop-color="#8a8a8c"/>
      </linearGradient>
    </defs>
    <circle cx="190" cy="190" r="170" fill="url(#decorFade)"/>
  </svg>

  <ul class="contact">
    <li class="address">20517 - 87 Ave. Edmonton,<br>AB, Canada. T6K 4N8</li>
    <li>
      <svg class="icon" viewBox="0 0 14 14" aria-hidden="true"><circle cx="7" cy="7" r="7" fill="var(--green)"/><path d="M4.5 3.5h1.6l.7 1.9-1 .7a5 5 0 0 0 2.1 2.1l.7-1 1.9.7v1.6c0 .4-.3.7-.7.7A6.2 6.2 0 0 1 3.8 4.2c0-.4.3-.7.7-.7z" fill="#262628"/></svg>
      +1 780.555.0184
    </li>
    <li>
      <svg class="icon" viewBox="0 0 14 14" aria-hidden="true"><circle cx="7" cy="7" r="7" fill="var(--green)"/><rect x="3.5" y="4.5" width="7" height="5" rx=".6" fill="#262628"/><path d="M3.8 4.9 7 7.4l3.2-2.5" stroke="var(--green)" stroke-width=".8" fill="none"/></svg>
      halya.dorosh@quillmail.example
    </li>
    <li>
      <svg class="icon" viewBox="0 0 14 14" aria-hidden="true"><circle cx="7" cy="7" r="7" fill="var(--green)"/><circle cx="7" cy="7" r="3.6" fill="none" stroke="#262628" stroke-width="1"/><path d="M3.4 7h7.2M7 3.4c-1.5 2-1.5 5.2 0 7.2M7 3.4c1.5 2 1.5 5.2 0 7.2" stroke="#262628" stroke-width=".8" fill="none"/></svg>
      brovix.example
    </li>
  </ul>
</section>

</body>
</html>
```